Fitness Centre/Personal Trainer Business Card

We need a business card design for a company based in Singapore called 'Vigor Ledger'.

We are a team of Personal Trainers and we are planning to open our new training facility.

This design will also be printed/painted on the walls in our gym.

We are a new breed of personal trainers who take fitness seriously and holistically. We do not merely train our clients to be big and muscular.

We believe in wholeness. In our opinion, fitness should include: strength, speed, flexibility, mobility, stamina & agility. These are what we train for. Of course, nutrition/diet is key.

We use fitness tools such as kettlebells, QVL, Pylometric boxes, battling ropes, clubbells, medicine balls, bulgarian bags etc - functional and non-bulky tools.

I currently have a Facebook page 'Vigor Ledger SG' which shows a logo of a kettlebell. But my business focus has since changed.

Services provided:
- Kettlebell Sport Preparation
- Calisthenics Training
- Corrective Exercises
- Sports Strength & Conditioning
- 28 days Weight Loss Program
- Myofascial Rehab Therapy
- Sports/Thai Massage

Main colors for the design should be BLACK & YELLOW. We envision a design which is able to protray the holistic view we take on fitness. Also it should somewhat appeal to the ladies and not intimidate them.

Target Market(s)

People between 18-35 years old. Students and working class alike.

Industry/Entity Type

Training

Requirements
Must have
• Name: Marcus Obadiah Lim
Fitness Coach
Corrective Exercise Specialist
M: +65 9437 2065
E: marcus@sgvigorledger-example.com

Double-sided please.
Nice to have
• "What is your vigor ledger?"

```html
<!DOCTYPE html>
<html lang="en">
<head>
<meta charset="utf-8">
<title>Vigor Ledger – Business Cards</title>
<link rel="stylesheet" href="https://fonts.googleapis.com/css2?family=Open+Sans:wght@400;600;700&display=swap">
<style>
  :root {
    --bg: #e9e7e3;
    --card-dark: #2b2b2b;
    --card-darker: #1c1c1c;
    --card-black: #050505;
    --tag-grey: #6a6a6a;
    --yellow: #f5d21c;
    --white: #ffffff;
    --text-light: #f1f1f1;
  }
  * { box-sizing: border-box; margin: 0; padding: 0; }
  html, body { width: 1200px; height: 722px; overflow: hidden; }
  body {
    background: var(--bg);
    position: relative;
    font-family: "Open Sans", Arial, sans-serif;
    color: var(--text-light);
  }
  .card {
    position: absolute;
    width: 514px;
    height: 293px;
    border-radius: 14px;
    overflow: hidden;
  }
  .card--front { left: 363px; top: 20px; background: linear-gradient(120deg, #3a3a3a 0%, var(--card-dark) 40%, var(--card-darker) 100%); }
  .card--back-grey { left: 94px; top: 376px; background: linear-gradient(120deg, #3a3a3a 0%, var(--card-dark) 45%, var(--card-darker) 100%); }
  .card--back-black { left: 639px; top: 383px; background: var(--card-black); }

  /* brand lockup standing in for the mark */
  .brand { position: absolute; display: flex; flex-direction: column; align-items: center; gap: 10px; }
  .brand__dot { width: 96px; height: 96px; border-radius: 50%; background: var(--yellow); }
  .brand__name { font-weight: 700; font-size: 24px; color: var(--yellow); white-space: nowrap; }
  .card--front .brand { left: 62px; top: 70px; }
  .card--back-grey .brand { left: 42px; top: 50px; }
  .card--back-grey .brand__dot { width: 120px; height: 120px; }
  .card--back-grey .brand__name { font-size: 28px; }

  /* rotated contact tag */
  .tag {
    position: absolute;
    left: 196px; top: 48px;
    width: 300px; height: 172px;
    background: var(--tag-grey);
    transform: rotate(-15deg);
    transform-origin: left top;
    padding: 16px 22px;
  }
  .tag__name { color: var(--yellow); font-weight: 700; font-size: 17px; }
  .tag__role { font-size: 13.5px; line-height: 1.35; color: var(--white); }
  .tag__contacts { list-style: none; margin-top: 16px; font-size: 13px; line-height: 1.4; color: var(--white); }
  .tag__contacts li { display: flex; align-items: center; gap: 6px; }
  .tag__contacts svg { width: 10px; height: 10px; flex: none; }
  .tagline { font-weight: 700; letter-spacing: 1.5px; color: var(--yellow); font-size: 15px; white-space: nowrap; }
  .card--front .tagline { position: absolute; left: 268px; top: 270px; transform: rotate(-15deg); transform-origin: left top; font-size: 14px; }

  /* services */
  .services__title { font-weight: 700; font-size: 19px; color: var(--yellow); }
  .services__list { list-style: none; }
  .services__list li::before { content: "• "; color: var(--white); }
  .card--back-grey .services { position: absolute; left: 266px; top: 26px; }
  .card--back-grey .services__title { margin-bottom: 12px; }
  .card--back-grey .services__list li { font-size: 15px; line-height: 26.5px; color: var(--white); }
  .card--back-grey .tagline { position: absolute; left: 0; right: 0; bottom: 18px; text-align: center; }

  .card--back-black .faint-name {
    position: absolute; left: 0; right: 0; top: 150px; text-align: center;
    font-weight: 700; font-size: 56px; color: var(--yellow); opacity: 0.18;
  }
  .card--back-black .services { position: absolute; left: 0; right: 0; top: 76px; text-align: center; }
  .card--back-black .services__title { margin-bottom: 14px; }
  .card--back-black .services__list { display: flex; flex-wrap: wrap; justify-content: center; column-gap: 10px; padding: 0 20px; }
  .card--back-black .services__list li { font-size: 17px; line-height: 32.5px; color: var(--white); white-space: nowrap; }
  .card--back-black .services__list li.break { flex-basis: 100%; height: 0; }
  .card--back-black .services__list li.break::before { content: none; }
  .card--back-black .tagline { position: absolute; left: 0; right: 0; bottom: 18px; text-align: center; font-size: 16px; }
</style>
</head>
<body>

<section class="card card--front" aria-label="Business card front">
  <div class="brand">
    <span class="brand__dot"></span>
    <span class="brand__name">Vigor Ledger</span>
  </div>
  <div class="tag">
    <p class="tag__name">Marcus Obadiah Lim</p>
    <p class="tag__role">Fitness Coach<br>Corrective Exercise Specialist</p>
    <ul class="tag__contacts">
      <li><svg viewBox="0 0 10 10"><rect x="2" y="0" width="6" height="10" rx="1" fill="#f5d21c"/></svg>+65 9437 2065</li>
      <li><svg viewBox="0 0 10 10"><rect x="0" y="2" width="10" height="7" fill="#f5d21c"/><path d="M0 2 L5 6 L10 2" stroke="#6a6a6a" fill="none"/></svg>marcus@sgvigorledger-example.com</li>
      <li><svg viewBox="0 0 10 10"><circle cx="5" cy="5" r="4" fill="none" stroke="#f5d21c" stroke-width="2"/></svg>www.sgvigorledger-example.com</li>
    </ul>
  </div>
  <p class="tagline">WHAT IS YOUR VIGOR LEDGER ?</p>
</section>

<section class="card card--back-grey" aria-label="Business card back, grey version">
  <div class="brand">
    <span class="brand__dot"></span>
    <span class="brand__name">Vigor Ledger</span>
  </div>
  <div class="services">
    <h2 class="services__title">Services</h2>
    <ul class="services__list">
      <li>Sports Strength &amp; Conditioning</li>
      <li>Kettlebell Sport Preparation</li>
      <li>28 days Weight Loss Program</li>
      <li>Myofascial Rehab Therapy</li>
      <li>Calisthenics Training</li>
      <li>Corrective Exercises</li>
      <li>Sports/Thai Massage</li>
    </ul>
  </div>
  <p class="tagline">WHAT IS YOUR VIGOR LEDGER ?</p>
</section>

<section class="card card--back-black" aria-label="Business card back, black version">
  <p class="faint-name" aria-hidden="true">Vigor Ledger</p>
  <div class="services">
    <h2 class="services__title">Services</h2>
    <ul class="services__list">
      <li>Sports Strength &amp; Conditioning</li>
      <li>Sports/Thai Massage</li>
      <li class="break"></li>
      <li>Kettlebell Sport Preparation</li>
      <li>Corrective Exercises</li>
      <li class="break"></li>
      <li>28 days Weight Loss Program</li>
      <li>Calisthenics Training</li>
      <li class="break"></li>
      <li>Myofascial Rehab Therapy</li>
    </ul>
  </div>
  <p class="tagline">WHAT IS YOUR VIGOR LEDGER ?</p>
</section>

</body>
</html>
```